Very new and innovative Web design for Property managers of Vacation rentals

We are looking for a new website design for travel agencies and property managers specialised on vacation rentals business, holiday villas and apartments.

The end users of this website are travellers who are looking for a vacation home for their next holiday: this is the reason why the website must be easy to use, attractive, professional, possibly elegant and focused on get new reservations.

This is a draft of our current website: https://intro3.kelumsito.com/
Please consider that we would like to have proposals with a totally different and innovative layout, surprise us!

These are the pages of the website:
• Homepage: feel free to redesign all the homepage as you wish, surprise us with something very new! Please consider that Property manager/Travel agencies usually want to have the opportunity to put in evidence groups of houses with specific characteristics (eg. villas with private swimming pool, apartment in big/small towns, villas with air co, etc…), destinations and tourist areas, and sometimes experiences or activities (please consider that the website layout must be suitable even if some of the previous sections are not used).
• Search page: we’d like to organise the results of the search page in three different ways:
o Grid
o Map
o List
• Property page: to illustrate the characteristics, descriptions, images, …. of the property. It is very important to put in evidence images of the property and to maintain the booking form (and the other call to action bottom – eg. whatsapp) always visible
• Custom pages: static pages composed usually by text, images and call to actions
• Contact us (general form)
• Info request (specific of a property form)
• Booking process
• Blog, organised in four pages:
o Home Page – introduction to the blog
o List of articles
o Single article
o Site Map (presentation of categories and sub-categories)

If possible, we’d prefer to receive the material in Adobe XD or similar so that we can obtain the three versions:
- smartphone
- tablet
- desktop

The website will be then developed in Bootstrap: as a result we’ll need the icons in SVG format (or the library used)

In attachment you can find the map of the website pages

```html
<!DOCTYPE html>
<html lang="en">
<head>
<meta charset="utf-8">
<title>Reservation Policy – Casaluce Stays</title>
<link rel="stylesheet" href="https://fonts.googleapis.com/css2?family=Montserrat:wght@300;400;500;600&family=Playfair+Display:wght@400;700&display=swap">
<style>
:root{
  --green:#15b387;
  --ink:#2b2b2b;
  --text:#555;
  --muted:#777;
  --footer:#1d1d1d;
  --footer-text:#b8b8b8;
  --white:#fff;
}
*{box-sizing:border-box;margin:0;padding:0}
html,body{width:722px;height:1200px;overflow:hidden;background:var(--white)}
body{font-family:"Montserrat",sans-serif;color:var(--ink);position:relative}

/* header */
.site-header{position:absolute;top:0;left:0;width:722px;height:55px}
.brand{position:absolute;left:68px;top:18px;display:flex;align-items:center;gap:5px;font-family:"Montserrat",sans-serif;font-weight:500;font-size:15px;color:var(--ink);letter-spacing:-.2px}
.brand-dot{width:12px;height:12px;border-radius:50%;background:var(--green)}
.utility-bar{position:absolute;right:0;top:0;width:235px;height:25px;background:var(--green);clip-path:polygon(0 0,100% 0,100% 100%,25px 100%);display:flex;align-items:center;justify-content:flex-end;gap:14px;padding-right:66px;color:var(--white);font-size:6.6px;font-weight:600}
.utility-bar span{display:flex;align-items:center;gap:3px}
.main-nav{position:absolute;top:37px;left:341px;display:flex;gap:0;font-size:7.6px;color:#333}
.main-nav a{color:inherit;text-decoration:none;margin-right:32px}
.main-nav a:last-child{margin-right:0}
.main-nav .active{color:var(--green);font-weight:600}

/* hero */
.hero{position:absolute;top:55px;left:0;width:722px;height:172px;background:linear-gradient(100deg,#6e5a2e 0%,#a3893f 14%,#5d5546 30%,#6d6658 55%,#8b7032 78%,#5c4d2c 100%);display:flex;align-items:center;justify-content:center}
.hero::after{content:"";position:absolute;inset:0;background:rgba(0,0,0,.32)}
.hero h1{position:relative;z-index:1;font-family:"Playfair Display",serif;font-weight:700;font-size:27px;color:var(--white);letter-spacing:.3px;margin-top:0}

/* breadcrumb */
.breadcrumb{position:absolute;top:247px;left:68px;font-size:7px;color:var(--muted)}
.breadcrumb .current{color:var(--ink)}
.breadcrumb .sep{margin:0 4px}

/* policy list */
.policy-list{position:absolute;top:285px;left:68px;width:587px}
.policy-item{display:flex;gap:17px;height:158px;margin-bottom:17.5px}
.policy-media{width:235px;height:158px;border-radius:3px;flex:none}
.media-vatican{background:linear-gradient(180deg,#102a6b 0%,#27408a 35%,#c69a4a 65%,#3a2c1c 100%)}
.media-pisa{background:linear-gradient(180deg,#3f86d8 0%,#a9c9ee 40%,#ece7dc 70%,#5f9a3a 100%)}
.media-pool{background:linear-gradient(180deg,#d7a06a 0%,#c9895d 45%,#3fa7b4 75%,#2a8fa0 100%)}
.media-colosseum{background:linear-gradient(180deg,#7ea3d4 0%,#b9c9dd 35%,#b08f6b 60%,#4d5a3a 100%)}
.policy-copy{padding-top:0}
.policy-kicker{font-size:11.6px;font-weight:300;color:#333;line-height:1;margin-top:0}
.policy-title{font-family:"Playfair Display",serif;font-weight:400;font-size:25px;line-height:29px;color:#1e1e1e;margin-top:7px;letter-spacing:.2px}
.policy-text{font-size:8.4px;line-height:15.8px;color:var(--text);margin-top:8px;font-weight:400}

/* footer */
.site-footer{position:absolute;top:1002px;left:0;width:722px;height:198px;background:var(--footer);color:var(--footer-text)}
.footer-brand{position:absolute;left:68px;top:78px;display:flex;align-items:center;gap:5px;font-weight:500;font-size:13px;color:var(--white)}
.footer-col{position:absolute;top:33px}
.footer-col h3{font-family:"Playfair Display",serif;font-weight:400;font-size:10.5px;color:var(--white);margin-bottom:10px}
.footer-col ul{list-style:none;font-size:7.8px;line-height:17px}
.col-links{left:202px}
.col-company{left:316px}
.col-contact{left:437px}
.col-follow{left:597px}
.contact-row{display:flex;gap:5px;font-size:7.8px;line-height:10px;margin-bottom:12px}
.contact-row svg{flex:none;margin-top:1px}
.social-row{display:flex;align-items:center;gap:5px;font-size:7.8px;margin-bottom:4px;height:17px}
.social-dot{width:16px;height:16px;border-radius:50%;background:var(--white)}
.copyright{position:absolute;top:155px;left:0;width:722px;text-align:center;font-size:6.8px;color:var(--footer-text)}
.copyright strong{color:var(--white);font-weight:400}
</style>
</head>
<body>

<header class="site-header">
  <div class="brand"><span class="brand-dot"></span>Casaluce Stays</div>
  <div class="utility-bar">
    <span><svg width="8" height="8" viewBox="0 0 10 10" fill="none" stroke="#fff" stroke-width="1"><circle cx="5" cy="3" r="2.2"/><path d="M1 9.5c0-2.4 1.8-3.6 4-3.6s4 1.2 4 3.6"/></svg>LOGIN</span>
    <span><svg width="9" height="8" viewBox="0 0 12 10" fill="none" stroke="#fff" stroke-width="1"><path d="M6 9.3 1.4 5A2.6 2.6 0 0 1 6 1.8 2.6 2.6 0 0 1 10.6 5Z"/></svg>WHISHLIST</span>
    <span>EN<svg width="5" height="4" viewBox="0 0 6 4" fill="none" stroke="#fff" stroke-width="1"><path d="M1 1l2 2 2-2"/></svg></span>
  </div>
  <nav class="main-nav">
    <a href="#">HOME</a>
    <a href="#">SEARCH</a>
    <a href="#">PROPERTY</a>
    <a href="#" class="active">CUSTOM</a>
    <a href="#">CONTACT US</a>
  </nav>
</header>

<section class="hero" role="img" aria-label="Bedroom with yellow curtains and a patterned bedspread">
  <h1>RESERVATION POLICY</h1>
</section>

<div class="breadcrumb">Home Page<span class="sep">/</span><span class="current">Reservation Policy</span></div>

<main class="policy-list">
  <article class="policy-item">
    <div class="policy-media media-vatican" role="img" aria-label="Illuminated basilica square at night"></div>
    <div class="policy-copy">
      <p class="policy-kicker">I must explain to you</p>
      <h2 class="policy-title">How all this mistaken idea<br>of&nbsp; Denouncing</h2>
      <p class="policy-text">Nam libero tempore, cum soluta nobis est eligendi optio cumque nihil impedit quo minus id quod maxime placeat facere possimus, omnis voluptas assumenda est, omnis dolor repellendus. Temporibus autem quibusdam et aut officiis debitis aut rerum necessitatibus saepe eveniet ut et voluptates...</p>
    </div>
  </article>
  <article class="policy-item">
    <div class="policy-media media-pisa" role="img" aria-label="Leaning tower and cathedral under a blue sky"></div>
    <div class="policy-copy">
      <p class="policy-kicker">I must explain to you</p>
      <h2 class="policy-title">How all this mistaken idea<br>of&nbsp; Denouncing</h2>
      <p class="policy-text">Nam libero tempore, cum soluta nobis est eligendi optio cumque nihil impedit quo minus id quod maxime placeat facere possimus, omnis voluptas assumenda est, omnis dolor repellendus. Temporibus autem quibusdam et aut officiis debitis aut rerum necessitatibus saepe eveniet ut et voluptates...</p>
    </div>
  </article>
  <article class="policy-item">
    <div class="policy-media media-pool" role="img" aria-label="Guest relaxing in a hotel swimming pool"></div>
    <div class="policy-copy">
      <p class="policy-kicker">I must explain to you</p>
      <h2 class="policy-title">How all this mistaken idea<br>of&nbsp; Denouncing</h2>
      <p class="policy-text">Nam libero tempore, cum soluta nobis est eligendi optio cumque nihil impedit quo minus id quod maxime placeat facere possimus, omnis voluptas assumenda est, omnis dolor repellendus. Temporibus autem quibusdam et aut officiis debitis aut rerum necessitatibus saepe eveniet ut et voluptates...</p>
    </div>
  </article>
  <article class="policy-item">
    <div class="policy-media media-colosseum" role="img" aria-label="Ancient amphitheatre at dusk"></div>
    <div class="policy-copy">
      <p class="policy-kicker">I must explain to you</p>
      <h2 class="policy-title">How all this mistaken idea<br>of&nbsp; Denouncing</h2>
      <p class="policy-text">Nam libero tempore, cum soluta nobis est eligendi optio cumque nihil impedit quo minus id quod maxime placeat facere possimus, omnis voluptas assumenda est, omnis dolor repellendus. Temporibus autem quibusdam et aut officiis debitis aut rerum necessitatibus saepe eveniet ut et voluptates...</p>
    </div>
  </article>
</main>

<footer class="site-footer">
  <div class="footer-brand"><span class="brand-dot"></span>Casaluce Stays</div>

  <div class="footer-col col-links">
    <h3>Quick Links</h3>
    <ul><li>Home</li><li>Search</li><li>Property</li><li>Custom</li><li>Contact Us</li></ul>
  </div>

  <div class="footer-col col-company">
    <h3>Company</h3>
    <ul><li>Privacy Policies</li><li>Reservation Policies</li><li>Cookie Policy</li></ul>
  </div>

  <div class="footer-col col-contact">
    <h3>Contact Us</h3>
    <div class="contact-row"><svg width="6" height="8" viewBox="0 0 6 8"><path d="M3 0a3 3 0 0 1 3 3c0 2-3 5-3 5S0 5 0 3a3 3 0 0 1 3-3Z" fill="#fff"/><circle cx="3" cy="3" r="1.1" fill="#1d1d1d"/></svg><span>Via dei Tigli 7 50120<br>Borgo Alto, Firenze (Italy)</span></div>
    <div class="contact-row"><svg width="6" height="8" viewBox="0 0 6 8"><path d="M1.2.3 2.4 0l.6 2-.9.6c.2 1 .8 2 1.6 2.6l.8-.5 1.4 1.4-.8 1C3 7 .3 4 .4 1.2Z" fill="#fff"/></svg><span>+39 055 4182907</span></div>
    <div class="contact-row"><svg width="8" height="6" viewBox="0 0 8 6"><rect width="8" height="6" fill="#fff"/><path d="M0 0l4 3.2L8 0" fill="none" stroke="#1d1d1d" stroke-width=".8"/></svg><span>info@casalucestays.com</span></div>
  </div>

  <div class="footer-col col-follow">
    <h3>Follow Us</h3>
    <div class="social-row"><span class="social-dot"></span>Friendwall</div>
    <div class="social-row"><span class="social-dot"></span>Chirper</div>
    <div class="social-row"><span class="social-dot"></span>Photoreel</div>
  </div>

  <p class="copyright">Copyright © 2021 <strong>Casaluce Stays</strong>. All rights reserved.</p>
</footer>

</body>
</html>
```